Bluecrest Learning Corps by graduating students from college in two years

Based on the logo design, create stationary and business cards for
Dr. Venrel T Oskamp, CEO, (555) 482-1736
and Marisa Deltoft, Respresentative, (301) 647-2208
Address: 4719 Pellham Court, Corlan Ridge, OH 43870
Incorporate elelments of the logo

Target Market(s)

USA

Font styles to use
Other font styles liked:
• match with the logo type style

```html
<!DOCTYPE html>
<html lang="en">
<head>
<meta charset="utf-8">
<title>Bluecrest Learning Corps — Stationery Set</title>
<link href="https://fonts.googleapis.com/css2?family=Open+Sans:wght@400&family=Tinos:wght@400;700&display=swap" rel="stylesheet">
<style>
  :root {
    --navy: #1f2559;
    --gold: #f2c12e;
    --paper: #ffffff;
    --cap-tint: #dcdce6;
    --scene-bg: #4b4b4b;
    --board-bg: #1b2020;
    --label: #f2f2f2;
    --ink-grey: #666a70;
    --rule: #9a9a9a;
  }
  * { box-sizing: border-box; margin: 0; padding: 0; }
  html, body { width: 784px; height: 1200px; overflow: hidden; }
  body { position: relative; background: var(--board-bg); font-family: "Tinos", "Times New Roman", serif; }

  .label { position: absolute; font-family: "Open Sans", Arial, sans-serif; font-size: 13px; color: var(--label); }

  .scene { position: absolute; left: 0; top: 0; width: 784px; height: 441px; background: var(--scene-bg); }

  .sheet { position: absolute; background: var(--paper); overflow: hidden; }

  .cap-art {
    position: absolute; left: 0; top: 0;
    background: linear-gradient(160deg, var(--cap-tint), #e6e6ee);
    clip-path: polygon(0 0, 72% 0, 100% 22%, 62% 100%, 0 100%);
  }

  .brand { position: absolute; display: flex; align-items: center; gap: 4px; color: var(--navy); font-family: "Tinos", serif; font-weight: 700; line-height: 1.05; }
  .brand .dot { flex: none; border-radius: 50%; background: var(--navy); }

  .contact { position: absolute; display: flex; align-items: center; gap: 3px; font-size: 5.6px; line-height: 1; color: var(--ink-grey); white-space: nowrap; }
  .contact .sep { color: var(--gold); }
  .contact svg { width: 6px; height: 6px; flex: none; }

  .footer-band { position: absolute; left: 0; right: 0; bottom: 0; background: var(--navy); }
  .footer-band::before, .footer-band::after { content: ""; position: absolute; left: 0; right: 0; height: 1px; background: var(--gold); }
  .footer-band::before { top: -4px; }
  .footer-band::after { top: -2px; }

  .note-lines { position: absolute; left: 11px; right: 11px; top: 74px; }
  .note-lines span { display: block; height: 13.4px; border-top: 0.6px solid var(--rule); }

  .compliments { position: absolute; right: 12px; bottom: 22px; font-size: 10px; line-height: 1; color: var(--navy); }

  .card-name { position: absolute; left: 16px; bottom: 34px; font-size: 10px; line-height: 1; color: var(--navy); white-space: nowrap; }
  .card-name b { font-weight: 700; }
  .card-name .sep { color: var(--gold); }
  .card-name .role { font-size: 8px; color: var(--ink-grey); }
  .card-rule { position: absolute; left: 16px; right: 16px; bottom: 30px; height: 0.6px; background: var(--rule); }
</style>
</head>
<body>

<section class="scene">
  <div class="label" style="left:64px;top:40px;">Stationery_16122025_5</div>

  <div class="sheet card-front" style="left:64px;top:130px;width:300px;height:172px;">
    <div class="brand" style="left:78px;top:70px;font-size:12px;">
      <span class="dot" style="width:14px;height:14px;"></span>Bluecrest Learning Corps
    </div>
  </div>

  <div class="sheet card-back" style="left:404px;top:130px;width:300px;height:172px;">
    <div class="cap-art" role="img" aria-label="Large faint graduation cap decoration" style="width:200px;height:150px;"></div>
    <div class="brand" style="right:12px;top:14px;font-size:8px;width:74px;">
      <span class="dot" style="width:10px;height:10px;"></span>Bluecrest Learning Corps
    </div>
    <div class="card-name"><b>Dr. Venrel T Oskamp</b> <span class="sep">|</span> <span class="role">CEO</span></div>
    <div class="card-rule"></div>
    <div class="contact" style="left:16px;bottom:17px;font-size:7px;">
      <svg viewBox="0 0 24 24"><path fill="#f2c12e" d="M6.6 10.8a15 15 0 0 0 6.6 6.6l2.2-2.2c.3-.3.7-.4 1-.2 1.1.4 2.3.6 3.6.6.6 0 1 .4 1 1V20c0 .6-.4 1-1 1A17 17 0 0 1 3 4c0-.6.4-1 1-1h3.5c.6 0 1 .4 1 1 0 1.3.2 2.5.6 3.6.1.3 0 .7-.2 1z"/></svg>
      (555) 482-1736 <span class="sep">|</span> 4719 Pellham Court, Corlan Ridge, OH 43870
    </div>
    <div class="footer-band" style="height:8px;"></div>
  </div>
</section>

<div class="label" style="left:64px;top:478px;">Letterhead_5</div>
<div class="sheet letterhead" style="left:64px;top:509px;width:311px;height:401px;">
  <div class="cap-art" role="img" aria-label="Large faint graduation cap decoration" style="width:250px;height:156px;"></div>
  <div class="brand" style="right:10px;top:14px;font-size:7.5px;width:70px;">
    <span class="dot" style="width:9px;height:9px;"></span>Bluecrest Learning Corps
  </div>
  <div class="contact" style="left:11px;bottom:19px;">
    <svg viewBox="0 0 24 24"><path fill="#f2c12e" d="M6.6 10.8a15 15 0 0 0 6.6 6.6l2.2-2.2c.3-.3.7-.4 1-.2 1.1.4 2.3.6 3.6.6.6 0 1 .4 1 1V20c0 .6-.4 1-1 1A17 17 0 0 1 3 4c0-.6.4-1 1-1h3.5c.6 0 1 .4 1 1 0 1.3.2 2.5.6 3.6.1.3 0 .7-.2 1z"/></svg>
    (555) 482-1736 <span class="sep">|</span> 4719 Pellham Court, Corlan Ridge, OH 43870
  </div>
  <div class="footer-band" style="height:10px;"></div>
</div>

<div class="label" style="left:410px;top:478px;">Note Pads_5</div>
<div class="sheet notepad" style="left:410px;top:509px;width:296px;height:207px;">
  <div class="cap-art" role="img" aria-label="Large faint graduation cap decoration" style="width:240px;height:155px;"></div>
  <div class="brand" style="right:10px;top:14px;font-size:7.5px;width:70px;">
    <span class="dot" style="width:9px;height:9px;"></span>Bluecrest Learning Corps
  </div>
  <div class="note-lines"><span></span><span></span><span></span><span></span><span></span><span></span><span></span><span></span></div>
  <div class="contact" style="left:11px;bottom:19px;">
    <svg viewBox="0 0 24 24"><path fill="#f2c12e" d="M6.6 10.8a15 15 0 0 0 6.6 6.6l2.2-2.2c.3-.3.7-.4 1-.2 1.1.4 2.3.6 3.6.6.6 0 1 .4 1 1V20c0 .6-.4 1-1 1A17 17 0 0 1 3 4c0-.6.4-1 1-1h3.5c.6 0 1 .4 1 1 0 1.3.2 2.5.6 3.6.1.3 0 .7-.2 1z"/></svg>
    (555) 482-1736 <span class="sep">|</span> 4719 Pellham Court, Corlan Ridge, OH 43870
  </div>
  <div class="footer-band" style="height:10px;"></div>
</div>

<div class="label" style="left:410px;top:740px;">Comp Slips_5</div>
<div class="sheet comp-slip" style="left:410px;top:772px;width:317px;height:146px;">
  <div class="cap-art" role="img" aria-label="Large faint graduation cap decoration" style="width:232px;height:130px;"></div>
  <div class="brand" style="right:10px;top:16px;font-size:7.5px;width:70px;">
    <span class="dot" style="width:9px;height:9px;"></span>Bluecrest Learning Corps
  </div>
  <div class="contact" style="left:11px;bottom:21px;">
    <svg viewBox="0 0 24 24"><path fill="#f2c12e" d="M6.6 10.8a15 15 0 0 0 6.6 6.6l2.2-2.2c.3-.3.7-.4 1-.2 1.1.4 2.3.6 3.6.6.6 0 1 .4 1 1V20c0 .6-.4 1-1 1A17 17 0 0 1 3 4c0-.6.4-1 1-1h3.5c.6 0 1 .4 1 1 0 1.3.2 2.5.6 3.6.1.3 0 .7-.2 1z"/></svg>
    (555) 482-1736 <span class="sep">|</span> 4719 Pellham Court, Corlan Ridge, OH 43870
  </div>
  <div class="compliments">With Compliments</div>
  <div class="footer-band" style="height:10px;"></div>
</div>

<div class="label" style="left:64px;top:957px;">ENV Front_5</div>
<div class="sheet env-front" style="left:64px;top:989px;width:318px;height:138px;">
  <div class="cap-art" role="img" aria-label="Large faint graduation cap decoration" style="width:230px;height:122px;"></div>
  <div class="brand" style="left:10px;top:12px;font-size:7.5px;width:70px;">
    <span class="dot" style="width:9px;height:9px;"></span>Bluecrest Learning Corps
  </div>
  <div class="contact" style="left:9px;bottom:18px;">4719 Pellham Court, Corlan Ridge, OH 43870</div>
  <div class="footer-band" style="height:10px;"></div>
</div>

<div class="label" style="left:410px;top:957px;">ENV Back_5</div>
<div class="sheet env-back" style="left:410px;top:989px;width:318px;height:138px;">
  <svg width="318" height="50" viewBox="0 0 318 50" style="position:absolute;left:0;top:0;">
    <path d="M0 0 H318 V2 Q312 14 300 16 L162 46 Q159 47 156 46 L18 16 Q6 14 2 2 Z" fill="#1f2559"/>
    <path d="M2 4 Q6 16 18 18 L156 48 Q159 49 162 48 L300 18 Q312 16 316 4" fill="none" stroke="#f2c12e" stroke-width="1.2"/>
  </svg>
</div>

</body>
</html>
```